4th Generation Family Business Needs a New Card Design!

We are a family owned 4th Generation company. We are based in the Sydney, Australia area and we are desperately in need of a more modern and classy card. We are monumental masons who design, supply & erect lasting memorials throughout cemeteries in Sydney. Our customers are normally in a period of grieving. I have attached logo files that will need to be implemented on the card. Company was established 1935. Australian Owned and Operated. Card needs to be designed to PIXO.com specification.

Target Market(s)

Our target market is based upon people that a grieving for family members that have passed away. We also deal with alot of companies that own and operate cemeteries.

Industry/Entity Type

Business

Contact Information for Business Card

Simon Harcourt, Operations Manager, 0417293086, simon@harcourtmemorials.com.au
Lewis Harcourt, Director, 0491630572, lewis@harcourtmemorials.com.au
Phone # 02 9561 3048
Website: www.harcourtmemorials.com.au
Address: Suite 17, 8 Palfrey Lane, West Carlow, Sydney NSW 2156

Font styles to use
Serif
Decorative
Script

Requirements
Must have
• Would like to see the logo nicely implemented with a modern design. Embossed lettering would be a nice additive.

```html
<!DOCTYPE html>
<html lang="en">
<head>
<meta charset="utf-8">
<title>Harcourt Memorials – Business Card</title>
<link rel="stylesheet" href="https://fonts.googleapis.com/css2?family=Cinzel:wght@600&family=Arimo:wght@400;700&display=swap">
<style>
  :root {
    --bg: #e9e6e1;
    --card-white: #ffffff;
    --card-black: #1f1f1f;
    --panel-top: #2e2e2e;
    --panel-bottom: #121212;
    --gold: #f2c21b;
    --ink: #222222;
    --paper-text: #f4f4f4;
  }
  * { box-sizing: border-box; margin: 0; padding: 0; }
  html, body { width: 1200px; height: 950px; overflow: hidden; }
  body {
    background: var(--bg);
    font-family: "Arimo", Arial, sans-serif;
    position: relative;
  }
  .card {
    position: absolute;
    top: 147px;
    width: 400px;
    height: 655px;
    border-radius: 4px;
    box-shadow: 0 10px 30px rgba(0,0,0,0.18);
    overflow: hidden;
  }
  .card--front { left: 170px; background: var(--card-white); }
  .card--back  { left: 630px; background: var(--card-black); }

  .wordmark {
    position: absolute;
    left: 0; right: 0;
    text-align: center;
    font-family: "Cinzel", Georgia, serif;
    font-weight: 600;
    line-height: 1;
  }
  .wordmark__name { display: block; font-size: 50px; letter-spacing: 2px; }
  .wordmark__sub  { display: block; font-size: 20px; letter-spacing: 6px; margin-top: 10px; }
  .card--front .wordmark { top: 150px; color: var(--ink); }
  .card--back  .wordmark { top: 290px; color: var(--paper-text); }

  .panel { position: absolute; left: 0; top: 300px; width: 400px; height: 355px; }
  .panel svg { display: block; }

  .contact {
    position: absolute;
    left: 62px;
    top: 370px;
    color: var(--paper-text);
    font-size: 15px;
    line-height: 1.45;
  }
  .contact__name { color: var(--gold); font-weight: 700; font-size: 19px; }
  .contact__role { font-size: 16px; margin-bottom: 10px; }
  .contact__label { color: var(--gold); font-weight: 700; }
</style>
</head>
<body>

  <section class="card card--front">
    <div class="wordmark">
      <span class="wordmark__name">HARCOURT</span>
      <span class="wordmark__sub">MEMORIALS</span>
    </div>

    <div class="panel">
      <svg width="400" height="355" viewBox="0 0 400 355">
        <defs>
          <linearGradient id="panelFill" x1="0" y1="0" x2="0" y2="1">
            <stop offset="0" stop-color="var(--panel-top)"/>
            <stop offset="1" stop-color="var(--panel-bottom)"/>
          </linearGradient>
        </defs>
        <path d="M0 40 H30 Q45 40 45 25 V15 Q45 0 60 0 H340 Q355 0 355 15 V25 Q355 40 370 40 H400 V355 H0 Z"
              fill="var(--gold)"/>
        <path d="M0 50 H32 Q55 50 55 28 V22 Q55 10 67 10 H333 Q345 10 345 22 V28 Q345 50 368 50 H400 V355 H0 Z"
              fill="url(#panelFill)"/>
      </svg>
    </div>

    <div class="contact">
      <p class="contact__name">Simon Harcourt</p>
      <p class="contact__role">Operations Manager</p>
      <p>Suite 17, 8 Palfrey Lane</p>
      <p>West Carlow, Sydney NSW 2156</p>
      <p><span class="contact__label">P</span> : 02 9561 3048</p>
      <p><span class="contact__label">M</span> : 0417293086</p>
      <p>simon@harcourtmemorials.com.au</p>
      <p>www.harcourtmemorials.com.au</p>
    </div>
  </section>

  <section class="card card--back">
    <div class="wordmark">
      <span class="wordmark__name">HARCOURT</span>
      <span class="wordmark__sub">MEMORIALS</span>
    </div>
  </section>

</body>
</html>
```